Business card for a new cabinet shop company named Veloran Cabinets for high end cabinets

Design a business card, thinking dark rich green with colours to speak of high end luxury ie; cream, gold, black possibly

Mitchell Tarrowby
Director Craftsman
Email: info@veloranjoinery-example.com.au
Instagram : @veloran.cabinets

```html
<!DOCTYPE html>
<html lang="en">
<head>
<meta charset="utf-8">
<title>Veloran Cabinets – Business Card</title>
<link rel="stylesheet" href="https://fonts.googleapis.com/css2?family=Montserrat:wght@400;500;700&display=swap">
<style>
  :root {
    --backdrop: #999999;
    --card-green: #1f3d3c;
    --gold: #c9aa6a;
    --cream-white: #ffffff;
  }
  * { margin: 0; padding: 0; box-sizing: border-box; }
  html, body {
    width: 1200px;
    height: 1059px;
    overflow: hidden;
    background: var(--backdrop);
    font-family: "Montserrat", sans-serif;
  }
  .card {
    position: absolute;
    left: 252px;
    width: 700px;
    height: 398px;
    background: var(--card-green);
    border-radius: 24px;
  }
  .card--front { top: 86px; }
  .card--back  { top: 570px; }

  .brand {
    position: absolute;
    left: 0;
    right: 0;
    display: flex;
    align-items: center;
    justify-content: center;
    gap: 14px;
    color: var(--gold);
    font-weight: 500;
    white-space: nowrap;
  }
  .brand__dot {
    border-radius: 50%;
    background: var(--gold);
    flex: none;
  }
  .card--front .brand { top: 90px; font-size: 42px; }
  .card--front .brand__dot { width: 22px; height: 22px; }
  .card--back .brand { top: 172px; font-size: 48px; }
  .card--back .brand__dot { width: 26px; height: 26px; }

  .person {
    position: absolute;
    right: 411px;
    top: 236px;
    text-align: right;
    white-space: nowrap;
  }
  .person__name {
    color: var(--gold);
    font-weight: 700;
    font-size: 26px;
    line-height: 1.2;
  }
  .person__role {
    color: var(--cream-white);
    font-weight: 400;
    font-size: 17px;
    margin-top: 8px;
  }
  .divider {
    position: absolute;
    left: 319px;
    top: 240px;
    width: 1px;
    height: 62px;
    background: var(--gold);
  }
  .contact {
    position: absolute;
    left: 343px;
    top: 247px;
    list-style: none;
  }
  .contact__item {
    display: flex;
    align-items: center;
    gap: 9px;
    color: var(--cream-white);
    font-size: 15px;
    font-weight: 400;
    height: 24px;
    margin-bottom: 11px;
    white-space: nowrap;
  }
  .contact__icon { width: 17px; height: 17px; flex: none; }
  .contact__social-dot {
    width: 15px;
    height: 15px;
    border-radius: 50%;
    border: 1.5px solid var(--gold);
    margin: 0 1px;
    flex: none;
  }
</style>
</head>
<body>
  <section class="card card--front">
    <div class="brand">
      <span class="brand__dot"></span>
      <span class="brand__name">Veloran Cabinets</span>
    </div>

    <div class="person">
      <p class="person__name">Mitchell Tarrowby</p>
      <p class="person__role">Director Craftsman</p>
    </div>

    <div class="divider"></div>

    <ul class="contact">
      <li class="contact__item">
        <svg class="contact__icon" viewBox="0 0 20 16" aria-hidden="true">
          <rect x="0" y="1" width="20" height="14" rx="1" fill="var(--gold)"/>
          <path d="M1 2 L10 9 L19 2" fill="none" stroke="var(--card-green)" stroke-width="2"/>
        </svg>
        <span>info@veloranjoinery-example.com.au</span>
      </li>
      <li class="contact__item">
        <span class="contact__social-dot"></span>
        <span>@veloran.cabinets</span>
      </li>
    </ul>
  </section>

  <section class="card card--back">
    <div class="brand">
      <span class="brand__dot"></span>
      <span class="brand__name">Veloran Cabinets</span>
    </div>
  </section>
</body>
</html>
```